BrivoNest Learning App for Children with Dyslexia

Project Description:

We are seeking a talented UI/UX designer to create engaging and intuitive designs for Brivonest, an innovative educational app designed to help children learn letters and words through a multisensory learning approach. The app aims to be particularly helpful for children with dyslexia, providing a supportive and interactive learning environment.

Key App Features & Design Requirements:

Account Creation Screen: Design a welcoming and straightforward sign-up page that allows users to register with their email or continue with Quarnix. The design should be clean, focusing on user-friendliness and accessibility, adhering to our terms of service and privacy policy.

Main Screen Design: The main screen should allocate at least 4/6 of its height to the interactive drawing area. It needs to display word prompts in both correct and scrambled orders and include options to "Show all Words," "Play all words," and a search function. The interface should be vibrant, engaging, and easy to navigate for children.

Profile Section: Create a user-friendly profile page that allows users to edit their profile image, name, username, email, links, and bio. The design should be clean and encourage user engagement.

BrivoTally Page: This section will display the user's learning progress, including rankings, a learning curve, and recently learned words. It should visually represent progress in a motivating and understandable way, suitable for a younger audience.

Visual and Auditory Feedback Implementation: Incorporate elements that support visual and auditory feedback, using dyslexia-friendly formats. This includes choosing appropriate colors, fonts, and auditory cues.

Accessibility and Customization Settings: Designs should include settings for adjusting visual contrast, font size, and the word list to accommodate individual preferences and needs.

Feel free to add more interactions and/or pages.

Design preferences:

Color Scheme: Use a bright, inviting color palette that stimulates learning and engagement without overwhelming the users.
Font Selection: Opt for fonts that are readable and accessible, particularly for users with dyslexia.
Icons and Graphics: Design custom icons and graphics that are cohesive with the app's theme and purpose. Illustrations should be simple, relatable, and supportive of the learning process.

Target Market(s)

Educational

Industry/Entity Type

Educational

Colors
0054AA
0677BA
7BADD7
CADEEF
E8F1F8
0094D4
00A9DD
6FCCEA
C7EBF8
E9F6FB

Requirements
Must have
• Educational app, a writing area, scoring and account management
Nice to have
• Statistics, Ranking Page, Settings and some nice visual features

```html
<!DOCTYPE html>
<html lang="en">
<head>
<meta charset="utf-8">
<title>Brivonest – App Screens</title>
<link rel="stylesheet" href="https://fonts.googleapis.com/css2?family=Figtree:wght@400;500;600;700&display=swap">
<style>
  :root {
    --bg: #f6f6f6;
    --white: #ffffff;
    --ink: #111111;
    --muted: #555555;
    --soft: #9a9a9a;
    --line: #dcdcdc;
    --sky: #00a9dd;
    --ocean: #0677ba;
    --deep: #0054aa;
    --canvas: #f1f2fb;
    --chip: #f0f0f2;
  }
  * { box-sizing: border-box; margin: 0; padding: 0; }
  html, body { width: 1200px; height: 649px; overflow: hidden; }
  body { background: var(--bg); font-family: "Figtree", sans-serif; color: var(--ink); position: relative; }

  .screen {
    position: absolute; top: 85px; width: 221px; height: 478px;
    background: var(--white); border-radius: 24px; overflow: hidden;
    box-shadow: 0 4px 18px rgba(0,0,0,.08);
  }
  .screen--signup { left: 115px; }
  .screen--main { left: 485px; }
  .screen--profile { left: 880px; }
  .abs { position: absolute; }
  .center { left: 0; right: 0; text-align: center; }

  .status { top: 28px; left: 6px; right: 8px; height: 14px; display: flex; justify-content: space-between; align-items: center; font-size: 10px; font-weight: 700; }
  .status svg { display: block; }
  .status__icons { display: flex; gap: 6px; align-items: center; }
  .status--light { color: var(--white); top: 31px; }

  /* sign-up */
  .brand { top: 56px; font-size: 19px; font-weight: 700; }
  .tagline { top: 84px; font-size: 7px; font-weight: 600; }
  .hero { top: 104px; left: 36px; width: 146px; height: 111px; border-radius: 73px 73px 0 0; background: linear-gradient(160deg, #cfe3ef 0%, #e9e4dc 55%, #d9b98e 100%); }
  .heading { top: 231px; font-size: 12.5px; font-weight: 600; }
  .subhead { top: 256px; font-size: 7px; font-weight: 600; color: var(--muted); }
  .field-email { top: 278px; left: 6px; width: 207px; height: 24px; border: 1px solid var(--line); border-radius: 12px; font-size: 7px; color: var(--soft); padding: 0 10px 0 12px; display: flex; align-items: center; justify-content: space-between; }
  .btn { display: flex; align-items: center; justify-content: center; color: var(--white); font-weight: 700; border-radius: 14px; background: linear-gradient(90deg, var(--ocean), var(--sky)); }
  .btn--signup { top: 311px; left: 6px; width: 207px; height: 25px; font-size: 7px; }
  .alt-label { top: 363px; left: 33px; font-size: 7px; font-weight: 600; color: var(--muted); }
  .alt-provider { top: 355px; left: 108px; width: 76px; height: 23px; border-radius: 12px; background: var(--white); box-shadow: 0 1px 5px rgba(0,0,0,.12); display: flex; align-items: center; justify-content: center; font-size: 10px; font-weight: 500; color: var(--ocean); }
  .legal { font-size: 7px; color: var(--muted); }
  .legal--one { top: 395px; }
  .legal--two { top: 411px; font-weight: 600; color: #333; }

  /* main */
  .topband { top: 0; left: 0; right: 0; height: 110px; background: var(--sky); }
  .panel { top: 99px; left: 0; right: 0; bottom: 0; background: var(--white); border-radius: 14px 14px 0 0; }
  .nav { top: 69px; left: 7px; right: 7px; height: 14px; display: flex; align-items: center; justify-content: space-between; color: var(--white); }
  .nav__title { position: absolute; left: 0; right: 0; text-align: center; font-size: 11px; font-weight: 700; }
  .nav__points { font-size: 7px; font-weight: 600; }
  .tools { top: 112px; left: 0; right: 0; display: flex; justify-content: center; gap: 14px; color: var(--ocean); }
  .tools span { width: 14px; height: 14px; display: flex; align-items: center; justify-content: center; font-family: Georgia, serif; font-weight: 700; font-size: 11px; }
  .draw-area { top: 139px; left: 6px; width: 208px; height: 174px; border-radius: 20px; background: var(--canvas); }
  .word-bar { top: 338px; left: 6px; width: 208px; height: 26px; border-radius: 13px; background: var(--white); box-shadow: 0 1px 5px rgba(0,0,0,.08); display: flex; align-items: center; justify-content: space-between; padding: 0 3px 0 13px; font-size: 8px; color: var(--soft); }
  .btn--play { width: 73px; height: 19px; font-size: 7.5px; border-radius: 10px; }
  .chip { top: 379px; width: 62px; height: 23px; border-radius: 12px; background: var(--chip); display: flex; align-items: center; justify-content: center; font-size: 7.5px; color: #444; }
  .btn--results { top: 420px; left: 6px; width: 208px; height: 22px; font-size: 8px; border-radius: 11px; }

  /* profile */
  .profile-nav { top: 66px; left: 10px; right: 9px; display: flex; justify-content: space-between; align-items: center; color: var(--white); }
  .profile-nav__title { font-size: 11px; font-weight: 700; }
  .avatar { top: 75px; left: 90px; width: 40px; height: 40px; border-radius: 50%; border: 2px solid var(--white); background: linear-gradient(160deg, #6b4a36, #d9a98a); }
  .profile-name { top: 120px; font-size: 10px; font-weight: 700; }
  .edit-link { top: 141px; font-size: 7.5px; font-weight: 500; color: var(--ocean); display: flex; justify-content: center; align-items: center; gap: 4px; }
  .label { left: 9px; font-size: 6.5px; font-weight: 500; }
  .field { left: 9px; width: 202px; height: 24px; border: 1px solid var(--line); border-radius: 12px; padding: 0 9px 0 10px; display: flex; align-items: center; justify-content: space-between; font-size: 6.5px; color: var(--soft); }
</style>
</head>
<body>

<!-- Sign-up screen -->
<section class="screen screen--signup" aria-label="Create account screen">
  <div class="abs status">
    <span>9:41</span>
    <span class="status__icons">
      <svg width="10" height="8" viewBox="0 0 10 8"><rect x="0" y="5" width="2" height="3" fill="currentColor"/><rect x="2.7" y="3.5" width="2" height="4.5" fill="currentColor"/><rect x="5.4" y="2" width="2" height="6" fill="currentColor"/><rect x="8" y="0" width="2" height="8" fill="currentColor"/></svg>
      <svg width="10" height="8" viewBox="0 0 10 8"><path d="M1 3a6 6 0 0 1 8 0M2.5 4.6a4 4 0 0 1 5 0" stroke="currentColor" stroke-width="1.2" fill="none"/><circle cx="5" cy="6.6" r="1" fill="currentColor"/></svg>
      <svg width="14" height="8" viewBox="0 0 14 8"><rect x=".5" y=".5" width="12" height="7" rx="1.5" stroke="currentColor" fill="none"/><rect x="2" y="2" width="9" height="4" fill="currentColor"/></svg>
    </span>
  </div>
  <h1 class="abs center brand">Brivonest</h1>
  <p class="abs center tagline">Learn letters and words</p>
  <div class="abs hero" role="img" aria-label="Photo of a teacher showing a letter card to a child"></div>
  <h2 class="abs center heading">Create an account</h2>
  <p class="abs center subhead">Enter your email to sign up for this app</p>
  <div class="abs field-email">
    <span>Enter email</span>
    <svg width="8" height="6" viewBox="0 0 8 6"><rect width="8" height="6" rx="1" fill="#9a9a9a"/><path d="M0.5 0.8 4 3.4 7.5 0.8" stroke="#fff" stroke-width=".8" fill="none"/></svg>
  </div>
  <div class="abs btn btn--signup">Sign up with email</div>
  <span class="abs alt-label">or continue with</span>
  <div class="abs alt-provider">Quarnix</div>
  <p class="abs center legal legal--one">By clicking continue, you agree to our and</p>
  <p class="abs center legal legal--two">Terms of Service, Privacy Policy</p>
</section>

<!-- Main screen -->
<section class="screen screen--main" aria-label="Main drawing screen">
  <div class="abs topband"></div>
  <div class="abs status status--light">
    <span>9:41</span>
    <span class="status__icons">
      <svg width="10" height="8" viewBox="0 0 10 8"><rect x="0" y="5" width="2" height="3" fill="currentColor"/><rect x="2.7" y="3.5" width="2" height="4.5" fill="currentColor"/><rect x="5.4" y="2" width="2" height="6" fill="currentColor"/><rect x="8" y="0" width="2" height="8" fill="currentColor"/></svg>
      <svg width="10" height="8" viewBox="0 0 10 8"><path d="M1 3a6 6 0 0 1 8 0M2.5 4.6a4 4 0 0 1 5 0" stroke="currentColor" stroke-width="1.2" fill="none"/><circle cx="5" cy="6.6" r="1" fill="currentColor"/></svg>
      <svg width="14" height="8" viewBox="0 0 14 8"><rect x=".5" y=".5" width="12" height="7" rx="1.5" stroke="currentColor" fill="none"/><rect x="2" y="2" width="9" height="4" fill="currentColor"/></svg>
    </span>
  </div>
  <div class="abs nav">
    <svg width="15" height="11" viewBox="0 0 15 11"><path d="M1 1.5h13M1 5.5h13M1 9.5h8" stroke="#fff" stroke-width="1.6" stroke-linecap="round"/></svg>
    <span class="nav__title">Main Screen</span>
    <span class="nav__points">16 Points</span>
  </div>
  <div class="abs panel"></div>
  <div class="abs tools">
    <span><svg width="11" height="11" viewBox="0 0 11 11"><path d="M1.5 9.5 2 7.3 7.6 1.7l1.7 1.7-5.6 5.6z" fill="currentColor"/></svg></span>
    <span><svg width="12" height="9" viewBox="0 0 12 9"><path d="M4 8.5 1 5.5 6 .5l5 3-3.5 5z" fill="none" stroke="currentColor" stroke-width="1.2"/><path d="M1 5.5 3 3.5l3.5 3L4 8.5z" fill="currentColor"/></svg></span>
    <span>A</span>
  </div>
  <div class="abs draw-area" aria-label="Drawing area"></div>
  <div class="abs word-bar">
    <span>Show all Words</span>
    <span class="btn btn--play">Play all words</span>
  </div>
  <div class="abs chip" style="left:7px">Word 1</div>
  <div class="abs chip" style="left:77px">Word 2</div>
  <div class="abs chip" style="left:151px">······</div>
  <div class="abs btn btn--results">Show me the results</div>
</section>

<!-- Profile screen -->
<section class="screen screen--profile" aria-label="Profile screen">
  <div class="abs topband"></div>
  <div class="abs status status--light">
    <span>9:41</span>
    <span class="status__icons">
      <svg width="10" height="8" viewBox="0 0 10 8"><rect x="0" y="5" width="2" height="3" fill="currentColor"/><rect x="2.7" y="3.5" width="2" height="4.5" fill="currentColor"/><rect x="5.4" y="2" width="2" height="6" fill="currentColor"/><rect x="8" y="0" width="2" height="8" fill="currentColor"/></svg>
      <svg width="10" height="8" viewBox="0 0 10 8"><path d="M1 3a6 6 0 0 1 8 0M2.5 4.6a4 4 0 0 1 5 0" stroke="currentColor" stroke-width="1.2" fill="none"/><circle cx="5" cy="6.6" r="1" fill="currentColor"/></svg>
      <svg width="14" height="8" viewBox="0 0 14 8"><rect x=".5" y=".5" width="12" height="7" rx="1.5" stroke="currentColor" fill="none"/><rect x="2" y="2" width="9" height="4" fill="currentColor"/></svg>
    </span>
  </div>
  <div class="abs panel"></div>
  <div class="abs profile-nav">
    <svg width="7" height="11" viewBox="0 0 7 11"><path d="M5.5 1 1.5 5.5l4 4.5" stroke="#fff" stroke-width="1.6" fill="none" stroke-linecap="round"/></svg>
    <span class="profile-nav__title">Profile</span>
  </div>
  <div class="abs avatar" role="img" aria-label="User profile photo"></div>
  <p class="abs center profile-name">Marta Quill</p>
  <p class="abs center edit-link">
    <svg width="8" height="8" viewBox="0 0 8 8"><rect width="8" height="8" rx="1.5" fill="#0677ba"/><path d="M2 6l.3-1.3L5.2 1.8l1 1L3.3 5.7z" fill="#fff"/></svg>
    Edit profile image
  </p>

  <span class="abs label" style="top:173px">Name</span>
  <div class="abs field" style="top:183px"><span>Marta Quill</span><svg width="7" height="4" viewBox="0 0 7 4"><path d="M.5.5 3.5 3.5 6.5.5" stroke="#888" fill="none"/></svg></div>
  <span class="abs label" style="top:222px">Username</span>
  <div class="abs field" style="top:232px"><span>@username</span><svg width="7" height="4" viewBox="0 0 7 4"><path d="M.5.5 3.5 3.5 6.5.5" stroke="#888" fill="none"/></svg></div>
  <span class="abs label" style="top:271px">Email</span>
  <div class="abs field" style="top:282px"><span>name@domain.com</span><svg width="7" height="4" viewBox="0 0 7 4"><path d="M.5.5 3.5 3.5 6.5.5" stroke="#888" fill="none"/></svg></div>
  <span class="abs label" style="top:322px">Links</span>
  <div class="abs field" style="top:332px"><span>mysite.page</span><svg width="7" height="4" viewBox="0 0 7 4"><path d="M.5.5 3.5 3.5 6.5.5" stroke="#888" fill="none"/></svg></div>
  <span class="abs label" style="top:372px">Bio</span>
  <div class="abs field" style="top:382px"><span>A description of this user.</span><svg width="4" height="7" viewBox="0 0 4 7"><path d="M.5.5 3.5 3.5.5 6.5" stroke="#888" fill="none"/></svg></div>
</section>

</body>
</html>
```